Executive Business Card for Healthcare Company [Need Today]

I need a business card design for a healthcare company. The only branding the company has thus far is a logo. The cards will be utilized by company executives. The design I envision will be vibrant and appealing but with a corporate feel. They shouldn't be too casual or playful. I would like to complete this project TODAY if possible.

Target Market(s)

Healthcare vendors, other executives in healthcare and pharmaceuticals

Industry/Entity Type

Pharmaceutical

Contact Information for Business Card

See attachment

Font styles to use
Serif
Sans Serif

Colors

Designer to choose colors to be used in the design.

```html
<!DOCTYPE html>
<html lang="en">
<head>
<meta charset="utf-8">
<title>Quellmont Therapeutics – Business Card</title>
<link href="https://fonts.googleapis.com/css2?family=Roboto:wght@300;400;500&display=swap" rel="stylesheet">
<style>
  :root {
    --backdrop: #4a4a4c;
    --card: #1c1d20;
    --silver: #8c8d91;
    --silver-dim: #55565a;
    --teal: #2bb3c0;
    --mint: #4cc79a;
    --text: #e6e7e9;
  }
  * { margin: 0; padding: 0; box-sizing: border-box; }
  html, body { width: 799px; height: 1200px; overflow: hidden; }
  body {
    background: var(--backdrop);
    font-family: "Roboto", Arial, sans-serif;
    position: relative;
  }
  .card {
    position: absolute;
    left: 80px;
    width: 640px;
    height: 366px;
    background: var(--card);
    border-radius: 3px;
    box-shadow: 0 14px 30px rgba(0,0,0,.45);
  }
  .card--front { top: 110px; }
  .card--back { top: 720px; }

  /* front */
  .front-mark {
    position: absolute; left: 52px; top: 70px;
    width: 130px; height: 130px; border-radius: 50%;
    border: 2px solid var(--silver-dim);
  }
  .front-divider {
    position: absolute; left: 196px; top: 112px;
    width: 1px; height: 46px; background: var(--silver-dim);
  }
  .front-name {
    position: absolute; left: 215px; top: 105px;
    font-weight: 300; font-size: 40px; line-height: 1.15;
    color: var(--silver);
  }
  .front-url {
    position: absolute; left: 52px; bottom: 56px;
    font-size: 17px; letter-spacing: 3px; color: var(--text);
  }

  /* back */
  .back-mark {
    position: absolute; left: 112px; top: 48px;
    width: 96px; height: 96px; border-radius: 50%;
    border: 3px solid var(--mint);
  }
  .back-name {
    position: absolute; left: 30px; top: 162px; width: 260px;
    font-weight: 300; font-size: 34px; line-height: 1.1;
    color: var(--teal); text-align: center;
  }
  .contact {
    position: absolute; left: 352px; top: 118px;
    color: var(--text);
  }
  .contact__name { font-size: 27px; font-weight: 400; color: var(--teal); }
  .contact__title { font-size: 13px; margin-top: 4px; color: #c9cacd; }
  .contact__list { list-style: none; margin-top: 18px; font-size: 17px; line-height: 1.35; }
  .contact__list li { display: flex; align-items: center; gap: 8px; }
  .contact__list svg { width: 14px; height: 14px; fill: var(--teal); flex: none; }
  .contact__address { font-size: 17px; line-height: 1.35; margin-top: 2px; }
</style>
</head>
<body>
  <section class="card card--front" aria-label="Card front">
    <div class="front-mark"></div>
    <div class="front-divider"></div>
    <div class="front-name">Quellmont<br>Therapeutics</div>
    <div class="front-url">www.quellmont.com</div>
  </section>

  <section class="card card--back" aria-label="Card back">
    <div class="back-mark"></div>
    <div class="back-name">Quellmont Therapeutics</div>
    <div class="contact">
      <div class="contact__name">Martin Hale</div>
      <div class="contact__title">Senior Director of Marketing</div>
      <ul class="contact__list">
        <li><svg viewBox="0 0 24 24"><path d="M6.6 10.8a15 15 0 0 0 6.6 6.6l2.2-2.2c.3-.3.7-.4 1-.2 1.1.4 2.3.6 3.6.6.6 0 1 .4 1 1V20c0 .6-.4 1-1 1A17 17 0 0 1 3 4c0-.6.4-1 1-1h3.5c.6 0 1 .4 1 1 0 1.3.2 2.5.6 3.6.1.3 0 .7-.2 1z"/></svg>555-214-0387</li>
        <li><svg viewBox="0 0 24 24"><path d="M7 1h10a2 2 0 0 1 2 2v18a2 2 0 0 1-2 2H7a2 2 0 0 1-2-2V3a2 2 0 0 1 2-2zm0 3v14h10V4zm5 15.5a1 1 0 1 0 0 2 1 1 0 0 0 0-2z"/></svg>555-318-6642</li>
        <li><svg viewBox="0 0 24 24"><path d="M12 2a10 10 0 1 0 0 20 10 10 0 0 0 0-20zm6.9 6h-3a15 15 0 0 0-1.3-3.9A8 8 0 0 1 18.9 8zM12 4c.8 1.2 1.5 2.5 1.9 4h-3.8c.4-1.5 1.1-2.8 1.9-4zM4.3 14a8 8 0 0 1 0-4h3.4a16 16 0 0 0 0 4zm.8 2h3a15 15 0 0 0 1.3 3.9A8 8 0 0 1 5.1 16zm3-8h-3a8 8 0 0 1 4.3-3.9C8.9 5.3 8.4 6.6 8.1 8zM12 20c-.8-1.2-1.5-2.5-1.9-4h3.8c-.4 1.5-1.1 2.8-1.9 4zm2.3-6H9.7a14 14 0 0 1 0-4h4.6a14 14 0 0 1 0 4zm.3 5.9c.6-1.2 1-2.5 1.3-3.9h3a8 8 0 0 1-4.3 3.9zm1.7-5.9a16 16 0 0 0 0-4h3.4a8 8 0 0 1 0 4z"/></svg>mhale@quellmont.com</li>
      </ul>
      <div class="contact__address">118 W Linden Avenue<br>Fairview, GA 30599</div>
    </div>
  </section>
</body>
</html>
```